Lorvex Tilo medical cannibis cultivation company

tag - Tilo rise
Lorvex Tilo medical cannabis cultivation - logo is selected- can we please see bold examples with our selection. We are mainly dealing with medical companies and professionals. We would like to be stand out in the crowd with our designs. Welcome any and all attempts. Thanks

Target Market(s)

Medical and Professional

Industry/Entity Type

Medical And Science

Font styles to use
Sans Serif

Colors

Designer to choose colors to be used in the design.

Requirements
Must have
• Bright colour and be bold- Love the teal and magenta that is currently on the dark background design.
Nice to have
• shading and the 3D affect- The shadowed appearance.
Should not have
• Anything related to illegal activity or un professional manners

```html
<!DOCTYPE html>
<html lang="en">
<head>
<meta charset="utf-8">
<title>Lorvex Tilo – Business Card</title>
<link rel="stylesheet" href="https://fonts.googleapis.com/css2?family=Cinzel:wght@600&family=Roboto:wght@400;500&display=swap">
<style>
  :root {
    --page-bg: #e8e8e8;
    --card-bg: #050505;
    --magenta: #9b4a9b;
    --cyan: #1caee6;
    --ring: #8a9096;
    --rule: #6f6f6f;
    --text-light: #f2f2f2;
    --text-soft: #d6d6d6;
  }
  * { margin: 0; padding: 0; box-sizing: border-box; }
  html, body {
    width: 1125px; height: 1200px; overflow: hidden;
    background: var(--page-bg);
  }
  .canvas { position: relative; width: 1125px; height: 1200px; }

  .card {
    position: absolute; left: 150px; width: 825px; height: 471px;
    background: var(--card-bg); border-radius: 22px; overflow: hidden;
  }
  .card--front { top: 98px; }
  .card--back { top: 631px; }

  /* brand placeholder: plain circle + name in the card's text font */
  .brand { position: absolute; text-align: center; }
  .brand__mark {
    display: block; margin: 0 auto; border-radius: 50%;
    border: 4px solid var(--ring);
  }
  .brand__name, .brand__tag {
    font-family: "Roboto", sans-serif; font-weight: 500; color: var(--cyan);
    white-space: nowrap; line-height: 1;
  }

  .card--front .brand { right: 39px; top: 34px; width: 240px; }
  .card--front .brand__mark { width: 136px; height: 136px; }
  .card--front .brand__name { font-size: 34px; margin-top: 26px; }
  .card--front .brand__tag { font-size: 15px; margin-top: 6px; letter-spacing: 2px; }

  .card--back .brand { left: 50%; transform: translateX(-50%); top: 92px; width: 380px; }
  .card--back .brand__mark { width: 170px; height: 170px; }
  .card--back .brand__name { font-size: 48px; margin-top: 30px; }
  .card--back .brand__tag { font-size: 20px; margin-top: 8px; letter-spacing: 3px; }

  /* person */
  .person { position: absolute; left: 41px; top: 216px; }
  .person__name {
    font-family: "Cinzel", serif; font-weight: 600; font-size: 30px;
    color: var(--magenta); line-height: 1;
  }
  .person__role {
    font-family: "Roboto", sans-serif; font-weight: 500; font-size: 20px;
    color: var(--cyan); margin-top: 8px; line-height: 1;
  }

  .divider {
    position: absolute; left: 44px; right: 39px; top: 292px;
    height: 2px; background: var(--rule);
  }

  .contacts {
    position: absolute; left: 41px; top: 316px; list-style: none;
    font-family: "Roboto", sans-serif; font-size: 20px; color: var(--text-light);
  }
  .contacts li { display: flex; align-items: center; height: 26.3px; }
  .contacts svg { width: 20px; height: 20px; margin-right: 11px; fill: var(--magenta); }

  .address {
    position: absolute; right: 38px; top: 339px; text-align: right;
    font-family: "Roboto", sans-serif; font-size: 20px; color: var(--text-soft);
    line-height: 26px; font-style: normal;
  }

  .band { position: absolute; bottom: 0; left: 0; width: 825px; height: 46px; }
  .website {
    position: absolute; right: 38px; bottom: 11px;
    font-family: "Roboto", sans-serif; font-size: 18px; letter-spacing: 4px;
    color: var(--text-light); line-height: 1;
  }
</style>
</head>
<body>
<main class="canvas">

  <section class="card card--front" aria-label="Business card front">
    <div class="brand">
      <span class="brand__mark"></span>
      <div class="brand__name">LORVEX TILO</div>
      <div class="brand__tag">TILO RISE</div>
    </div>

    <div class="person">
      <h1 class="person__name">MARA QUILLEN</h1>
      <p class="person__role">CEO/FOUNDER</p>
    </div>

    <div class="divider"></div>

    <ul class="contacts">
      <li>
        <svg viewBox="0 0 24 24" aria-hidden="true"><path d="M6.6 10.8a15.2 15.2 0 0 0 6.6 6.6l2.2-2.2a1 1 0 0 1 1-.25 11.4 11.4 0 0 0 3.6.57 1 1 0 0 1 1 1V20a1 1 0 0 1-1 1A17 17 0 0 1 3 4a1 1 0 0 1 1-1h3.5a1 1 0 0 1 1 1c0 1.250.2 2.45.57 3.57a1 1 0 0 1-.25 1z"/></svg>
        555 210 4417
      </li>
      <li>
        <svg viewBox="0 0 24 24" aria-hidden="true"><path d="M7 1h10a2 2 0 0 1 2 2v18a2 2 0 0 1-2 2H7a2 2 0 0 1-2-2V3a2 2 0 0 1 2-2zm0 3v14h10V4zm5 15.5a1 1 0 1 0 0 2 1 1 0 0 0 0-2z"/></svg>
        555 387 1092
      </li>
      <li>
        <svg viewBox="0 0 24 24" aria-hidden="true"><path d="M7 2h8l3 3v4H6V3a1 1 0 0 1 1-1zM3 10h18a2 2 0 0 1 2 2v6h-4v4H5v-4H1v-6a2 2 0 0 1 2-2zm4 6v4h10v-4z"/></svg>
        555 764 2305
      </li>
      <li>
        <svg viewBox="0 0 24 24" aria-hidden="true"><path d="M3 5h18a1 1 0 0 1 1 1v12a1 1 0 0 1-1 1H3a1 1 0 0 1-1-1V6a1 1 0 0 1 1-1zm1 2.2V17h16V7.2l-8 5.3z"/></svg>
        mara@lorvextilo.com
      </li>
    </ul>

    <address class="address">4120 Birchwood Row<br>Kenmore, Alaska 99501</address>

    <svg class="band" viewBox="0 0 825 46" aria-hidden="true">
      <polygon points="0,27 465,27 452,46 0,46" fill="var(--magenta)"/>
      <polygon points="479,0 825,0 825,46 458,46" fill="var(--cyan)"/>
    </svg>
    <p class="website">www.lorvextilo.com</p>
  </section>

  <section class="card card--back" aria-label="Business card back">
    <div class="brand">
      <span class="brand__mark"></span>
      <div class="brand__name">LORVEX TILO</div>
      <div class="brand__tag">TILO RISE</div>
    </div>
  </section>

</main>
</body>
</html>
```